Skin cancer clinic services trifold brochure

Need trifold brochure listing skin cancer services our clinic provides, staff information, location and brief about skin cancer with colours similar to our web site www.Tolvarin.clinic. I will provide more information regarding services and staff but want this colourful and standout as it will be given to other referring doctors or patients

Target Market(s)

Age 40 to 80 years

Industry/Entity Type

Medical

Font styles to use
Serif

Colors

Designer to choose colors to be used in the design.

Requirements
Must have
• Logo, services, contact info, beach or sun look and colours similar to web site or logo

```html
<!DOCTYPE html>
<html lang="en">
<head>
<meta charset="utf-8">
<title>Tolvarin Skin Cancer Clinic – Trifold Brochure</title>
<link rel="stylesheet" href="https://fonts.googleapis.com/css2?family=Arvo:wght@400;700&family=Pacifico&display=swap">
<style>
  :root {
    --page-bg: #9a9a9a;
    --paper: #ffffff;
    --sun-yellow: #f8e400;
    --sun-amber: #f2a51e;
    --sun-orange: #e8791a;
    --band-tan: #e7b15c;
    --ink-navy: #2b2f52;
    --ink-body: #3a3a3a;
    --sea-light: #bfe0f2;
    --sea-deep: #3f8fbf;
    --sand: #b98e55;
    --sand-dark: #8c6a3c;
    --skin-warm: #8a5a3e;
    --hat-straw: #c9a06a;
  }
  * { box-sizing: border-box; margin: 0; padding: 0; }
  html, body { width: 1200px; height: 900px; overflow: hidden; }
  body {
    background: var(--page-bg);
    font-family: "Arvo", Georgia, serif;
    position: relative;
  }
  .brochure {
    position: absolute;
    left: 72px; top: 42px;
    width: 1056px; height: 816px;
    display: flex;
    background: var(--paper);
  }
  .panel {
    position: relative;
    width: 352px; height: 816px;
    overflow: hidden;
  }
  .panel-art { position: absolute; inset: 0; width: 352px; height: 816px; }

  /* Left panel */
  .intro { position: absolute; left: 34px; top: 48px; width: 290px; }
  .intro-title {
    color: var(--sun-orange);
    font-size: 23px; font-weight: 700; line-height: 1.08;
    text-transform: uppercase; letter-spacing: 0.5px;
  }
  .intro-text {
    color: var(--ink-body);
    font-size: 12.5px; line-height: 1.35;
    margin-top: 12px;
  }
  .urgent { position: absolute; left: 34px; top: 660px; width: 290px; color: var(--ink-navy); }
  .urgent-question { font-size: 15px; line-height: 1.25; font-weight: 700; }
  .urgent-cta { font-size: 19px; font-weight: 700; margin-top: 18px; letter-spacing: 0.5px; }

  /* Middle panel */
  .contact {
    position: absolute; left: 0; top: 370px; width: 352px;
    display: flex; flex-direction: column; align-items: center;
    color: var(--ink-navy); text-align: center;
  }
  .contact-icon { width: 44px; height: 44px; }
  .contact-address { font-size: 15px; font-weight: 700; line-height: 1.3; margin: 8px 0 22px; }
  .contact-phone { font-size: 24px; font-weight: 700; margin: 8px 0 20px; }
  .contact-web { font-size: 22px; font-weight: 700; margin-top: 26px; }

  /* Right panel */
  .brand {
    position: absolute; left: 30px; top: 40px;
    display: flex; align-items: center; gap: 10px;
  }
  .brand-mark { width: 26px; height: 26px; border-radius: 50%; background: var(--sun-orange); }
  .brand-name { font-size: 26px; font-weight: 700; color: var(--ink-navy); letter-spacing: 1px; }
  .tagline {
    position: absolute; right: 28px; top: 560px; width: 300px;
    font-family: "Pacifico", cursive;
    color: var(--ink-navy);
    text-align: right; line-height: 1.15;
  }
  .tagline-big { display: block; font-size: 46px; }
  .tagline-small { display: block; font-size: 34px; }
</style>
</head>
<body>
<main class="brochure">

  <section class="panel panel-inside-flap">
    <svg class="panel-art" viewBox="0 0 352 816" aria-hidden="true">
      <defs>
        <linearGradient id="sunFillLeft" x1="0" y1="0" x2="1" y2="0.4">
          <stop offset="0" stop-color="#f8e400"/>
          <stop offset="1" stop-color="#f0a020"/>
        </linearGradient>
        <linearGradient id="hatPhoto" x1="0" y1="0" x2="1" y2="1">
          <stop offset="0" stop-color="#efeae2"/>
          <stop offset="0.45" stop-color="#c9a06a"/>
          <stop offset="1" stop-color="#7b4d34"/>
        </linearGradient>
      </defs>
      <rect x="0" y="0" width="352" height="12" fill="var(--band-tan)"/>
      <rect x="0" y="12" width="352" height="300" fill="var(--paper)"/>
      <rect x="0" y="290" width="352" height="322" fill="url(#hatPhoto)" role="img" aria-label="Photo of a person in a straw sun hat with freckled, sun-exposed shoulders"/>
      <polygon points="0,606 352,598 352,610 0,618" fill="var(--band-tan)"/>
      <polygon points="0,618 352,610 352,816 0,816" fill="url(#sunFillLeft)"/>
    </svg>
    <div class="intro">
      <h2 class="intro-title">When was your<br>last skin check?</h2>
      <p class="intro-text">Tolvarin is a leading coastal skin cancer clinic based in Lindale Bay.</p>
      <p class="intro-text">Headed by qualified professional Dr Maren Holloway, Tolvarin engages the latest technology and clinical care to identify the best treatments and preventative measures for clients.</p>
    </div>
    <div class="urgent">
      <p class="urgent-question">Do you have a<br>suspicious lesion that you<br>need evaluated immediately?</p>
      <p class="urgent-cta">BOOK AN URGENT APPOINTMENT</p>
    </div>
  </section>

  <section class="panel panel-back">
    <svg class="panel-art" viewBox="0 0 352 816" aria-hidden="true">
      <defs>
        <linearGradient id="seaPhoto" x1="0" y1="0" x2="0" y2="1">
          <stop offset="0" stop-color="#f3c23a"/>
          <stop offset="0.3" stop-color="#bfe0f2"/>
          <stop offset="0.7" stop-color="#3f8fbf"/>
          <stop offset="1" stop-color="#9fcbe0"/>
        </linearGradient>
        <linearGradient id="sunFillMid" x1="0" y1="0" x2="1" y2="0.6">
          <stop offset="0" stop-color="#f8e400"/>
          <stop offset="1" stop-color="#f0a020"/>
        </linearGradient>
      </defs>
      <rect x="0" y="0" width="352" height="336" fill="url(#seaPhoto)" role="img" aria-label="Photo of a child with arm floaties splashing in shallow sea water"/>
      <polygon points="0,330 352,326 352,338 0,342" fill="var(--band-tan)"/>
      <polygon points="0,342 352,338 352,816 0,816" fill="url(#sunFillMid)"/>
    </svg>
    <address class="contact">
      <svg class="contact-icon" viewBox="0 0 44 44" aria-hidden="true">
        <circle cx="22" cy="22" r="19" fill="none" stroke="var(--ink-navy)" stroke-width="2.5"/>
        <text x="22" y="29" text-anchor="middle" font-family="Arvo, serif" font-size="20" font-weight="700" fill="var(--ink-navy)">@</text>
      </svg>
      <p class="contact-address">Suites 3 &amp; 4 117 Coral Parade<br>Lindale Bay NSW 2261</p>
      <svg class="contact-icon" viewBox="0 0 44 44" aria-hidden="true">
        <circle cx="22" cy="22" r="19" fill="none" stroke="var(--ink-navy)" stroke-width="2.5"/>
        <path d="M15 13 l5 -1 l2 6 l-3 2 q2 5 6 7 l2 -3 l6 2 l-1 5 q-13 1 -17 -18z" fill="var(--ink-navy)"/>
      </svg>
      <p class="contact-phone">1300 587 614</p>
      <svg class="contact-icon" viewBox="0 0 44 44" aria-hidden="true">
        <circle cx="22" cy="22" r="19" fill="none" stroke="var(--ink-navy)" stroke-width="2.5"/>
        <g fill="none" stroke="var(--ink-navy)" stroke-width="1.8">
          <circle cx="22" cy="22" r="11"/>
          <ellipse cx="22" cy="22" rx="5" ry="11"/>
          <line x1="11" y1="22" x2="33" y2="22"/>
          <line x1="13" y1="16" x2="31" y2="16"/>
          <line x1="13" y1="28" x2="31" y2="28"/>
        </g>
      </svg>
      <p class="contact-web">www.Tolvarin.clinic</p>
    </address>
  </section>

  <section class="panel panel-cover">
    <svg class="panel-art" viewBox="0 0 352 816" aria-hidden="true">
      <defs>
        <linearGradient id="sandPhoto" x1="0" y1="0" x2="1" y2="1">
          <stop offset="0" stop-color="#e9eef0"/>
          <stop offset="0.25" stop-color="#c8a36b"/>
          <stop offset="0.6" stop-color="#b98e55"/>
          <stop offset="1" stop-color="#8c6a3c"/>
        </linearGradient>
        <linearGradient id="sunFillRight" x1="0" y1="1" x2="1" y2="0">
          <stop offset="0" stop-color="#f0a020"/>
          <stop offset="1" stop-color="#f8e400"/>
        </linearGradient>
      </defs>
      <rect x="0" y="0" width="352" height="816" fill="url(#sunFillRight)"/>
      <polygon points="0,0 352,0 352,430 0,560" fill="url(#sandPhoto)" role="img" aria-label="Photo of a red starfish on wet sand at the edge of a breaking wave"/>
      <polygon points="0,0 352,0 352,20 150,0 0,150" fill="var(--paper)"/>
      <polygon points="0,0 250,0 0,160" fill="var(--paper)"/>
    </svg>
    <div class="brand">
      <span class="brand-mark" aria-hidden="true"></span>
      <span class="brand-name">TOLVARIN</span>
    </div>
    <h1 class="tagline">
      <span class="tagline-big">Comfort</span>
      <span class="tagline-small">in your Skin</span>
    </h1>
  </section>

</main>
</body>
</html>
```